HearthMile business card and stationary design

We are looking for a simple yet elegant design for our mortgage company business card and stationary.

The card should include:
Name (Marcus Pell)
Title (CEO)
Phone Number (732-555-0182)
Address (48 Birchwell Court, Suite 314, Alderby, NJ 07791)
Email (email@hearthmile.example)
"NMLS" i.e. (NMLS 61947)
"Company NMLS" (Company NMLS 274615)

Contact Information for Business Card

See above

```html
<!DOCTYPE html>
<html lang="en">
<head>
<meta charset="utf-8">
<title>HearthMile Business Card</title>
<link rel="stylesheet" href="https://fonts.googleapis.com/css2?family=Montserrat:wght@700&family=Arimo:wght@400&display=swap">
<style>
  :root {
    --navy: #1b2631;
    --sky: #00aeef;
    --white: #ffffff;
    --backdrop: #e9ebee;
    --frost-light: #f7f7f8;
    --frost-mid: #e3e1e3;
    --frost-edge: #cfcdd0;
  }
  * { box-sizing: border-box; margin: 0; padding: 0; }
  html, body { width: 1200px; height: 900px; overflow: hidden; }
  body { background: var(--backdrop); position: relative; }

  .business-card {
    position: absolute; left: 100px; top: 141px;
    width: 1000px; height: 617px;
    background: var(--navy);
    overflow: hidden;
    font-family: "Arimo", Arial, sans-serif;
    color: var(--white);
    box-shadow: 0 10px 30px rgba(0,0,0,0.18);
  }
  .accent-band {
    position: absolute; left: 672px; top: 0; width: 328px; height: 100%;
    background: var(--sky);
  }
  .brand-disc {
    position: absolute; left: 423px; top: 43px; width: 532px; height: 532px;
    border-radius: 50%;
    background: radial-gradient(circle at 45% 40%, var(--frost-light) 0%, var(--frost-mid) 65%, var(--frost-edge) 100%);
    display: flex; align-items: center; justify-content: center;
  }
  .brand-name {
    font-family: "Arimo", Arial, sans-serif;
    font-weight: 400;
    font-size: 72px;
    color: var(--navy);
    letter-spacing: 0.5px;
  }

  .person-name {
    position: absolute; left: 47px; top: 62px;
    font-family: "Montserrat", Arial, sans-serif; font-weight: 700;
    font-size: 42px; color: var(--sky); letter-spacing: -0.5px;
  }
  .person-title {
    position: absolute; left: 47px; top: 107px; font-size: 27px;
  }
  .contact-list {
    position: absolute; left: 47px; top: 178px; list-style: none;
    font-size: 27px; line-height: 37px;
  }
  .contact-item { display: flex; align-items: center; gap: 8px; }
  .contact-icon { width: 28px; height: 28px; flex: none; }
  .highlight { color: var(--sky); }
  .office-address {
    position: absolute; left: 49px; top: 322px;
    font-size: 27px; line-height: 36px; font-style: normal;
  }
  .licensing {
    position: absolute; left: 56px; top: 482px;
    font-size: 27px; line-height: 36px;
  }
</style>
</head>
<body>
  <div class="business-card">
    <div class="accent-band"></div>
    <div class="brand-disc"><span class="brand-name">HearthMile</span></div>

    <h1 class="person-name">Marcus Pell</h1>
    <p class="person-title">CEO</p>

    <ul class="contact-list">
      <li class="contact-item">
        <svg class="contact-icon" viewBox="0 0 24 24" aria-hidden="true"><path fill="#00aeef" d="M6.6 10.8a15.1 15.1 0 0 0 6.6 6.6l2.2-2.2a1 1 0 0 1 1-.25 11.4 11.4 0 0 0 3.6.57 1 1 0 0 1 1 1V20a1 1 0 0 1-1 1A17 17 0 0 1 3 4a1 1 0 0 1 1-1h3.5a1 1 0 0 1 1 1c0 1.25.2 2.45.57 3.57a1 1 0 0 1-.25 1z"/></svg>
        <span>732-555-0182</span>
      </li>
      <li class="contact-item">
        <svg class="contact-icon" viewBox="0 0 24 24" aria-hidden="true"><rect x="2" y="5" width="20" height="14" fill="#00aeef"/><path d="M2 5l10 8 10-8" fill="none" stroke="#1b2631" stroke-width="1.6"/></svg>
        <span>email@hearthmile.example</span>
      </li>
      <li class="contact-item">
        <svg class="contact-icon" viewBox="0 0 24 24" aria-hidden="true"><g fill="none" stroke="#00aeef" stroke-width="1.6"><circle cx="12" cy="12" r="9.5"/><ellipse cx="12" cy="12" rx="4.2" ry="9.5"/><path d="M2.5 12h19M4 7h16M4 17h16"/></g></svg>
        <span>www.<span class="highlight">hearthmile</span>.example</span>
      </li>
    </ul>

    <address class="office-address">48 Birchwell Court, Suite 314<br>Alderby, NJ 07791</address>

    <div class="licensing">
      <p><span class="highlight">NMLS</span> 61947</p>
      <p><span class="highlight">Company NMLS</span> 274615</p>
    </div>
  </div>
</body>
</html>
```